Professional Single Page Website Design for Tollbrook Advisory

Tollbrook Advisory is a new business consultancy specializing in providing expert services to small businesses, primarily in the brick-and-mortar retail and food service sectors. We offer a range of services including franchise development and launch, due diligence, and construction management.

Currently, we have a basic website set up at www.tollbrookadvisory.example, but we need a professional touch to enhance its design and functionality.

Project Requirements:
- Single Page Design: For now, we need a single page design that effectively showcases who we are, our services, and contact information.
- Future Expansion: The design should be flexible and scalable for future expansion to include additional pages like specific service offerings, about us, and a dedicated contact page.
- Design Aesthetic: We are looking for a modern yet professional design that aligns with our brand identity.
- Logo: We have a logo that we like, which was also sourced from Pixel Bazaar. The logo files are attached to this project brief.

Key Sections to Include:
- Hero Section: An engaging introduction to Tollbrook Advisory with a strong visual impact.
- About Us: A brief overview of who we are and our mission.
- Team: Section for the profiles of the two principals.
- Services: A clear and concise presentation of our services, including franchise development, due diligence, and construction management.
- Contact Information: Easy-to-find contact details, including a form for inquiries.
- Call to Action: Encouraging visitors to get in touch with us for consultations or further information.

Design Considerations:
- Ensure the design is responsive and mobile-friendly.
- Include high-quality images and icons that complement our services and industry.
- We do not need development services, this is only a design project.

```html
<!DOCTYPE html>
<html lang="en">
<head>
<meta charset="utf-8">
<title>Tollbrook Advisory</title>
<link href="https://fonts.googleapis.com/css2?family=Poppins:wght@400;500;600;700&family=Lato:wght@400;700&display=swap" rel="stylesheet">
<style>
:root{
  --green:#8ec6a8;
  --green-dark:#6fb08e;
  --ink:#1f2a33;
  --ink-soft:#2b3944;
  --text:#333a40;
  --line:#c9d0d4;
  --light:#eef4f2;
  --white:#ffffff;
}
*{margin:0;padding:0;box-sizing:border-box}
html,body{width:1200px;height:3896px;overflow:hidden}
body{position:relative;background:var(--white);font-family:'Lato',sans-serif;color:var(--text)}
.abs{position:absolute}
.h-font{font-family:'Poppins',sans-serif}
.btn{position:absolute;display:flex;align-items:center;justify-content:center;border-radius:30px;background:var(--green);color:var(--white);font-family:'Poppins',sans-serif;font-weight:600;font-size:15px;box-shadow:0 4px 10px rgba(0,0,0,.12)}
.section-title{position:absolute;left:0;width:1200px;text-align:center;font-family:'Poppins',sans-serif;font-weight:600;font-size:32px;color:var(--ink)}
.section-title .accent{color:var(--green)}
.section-rule{position:absolute;left:575px;width:50px;height:3px;background:var(--ink)}

/* header */
.site-header{top:0;left:0;width:1200px;height:89px;background:var(--white)}
.brand{display:flex;align-items:center;gap:12px}
.brand-dot{width:40px;height:40px;border-radius:50%;background:var(--green)}
.brand-name{font-family:'Poppins',sans-serif;font-weight:600;font-size:22px;color:var(--ink)}
.nav a{position:absolute;top:34px;font-family:'Poppins',sans-serif;font-size:17px;color:var(--ink);text-decoration:none}

/* hero */
.hero{top:89px;left:0;width:1200px;height:601px;background:linear-gradient(90deg,#2a3a44 0%,#344753 45%,#6b7a82 70%,#8d9799 100%)}
.hero-photo{top:0;left:480px;width:720px;height:601px;background:linear-gradient(90deg,rgba(52,71,83,0) 0%,rgba(120,128,126,.5) 40%,rgba(165,160,150,.55) 100%)}
.hero h1{top:140px;left:97px;width:520px;font-family:'Poppins',sans-serif;font-weight:600;font-size:48px;line-height:63px;color:var(--white)}
.hero p{top:284px;left:97px;width:470px;font-size:15px;line-height:31px;color:var(--white)}

/* about */
.about-frame-back{top:895px;left:106px;width:474px;height:445px;border:2px solid var(--ink)}
.about-frame-front{top:872px;left:86px;width:474px;height:445px;border:2px solid var(--green)}
.about-photo{top:885px;left:98px;width:470px;height:440px;background:linear-gradient(135deg,#9aa3a3 0%,#c7c1b2 45%,#7b7364 100%)}
.about-block h3{font-family:'Poppins',sans-serif;font-weight:600;font-size:27px;color:var(--ink)}
.about-text{font-size:15px;line-height:31px;color:var(--text)}
.about-divider{top:1089px;left:644px;width:457px;height:2px;background:var(--line)}

/* services */
.services{top:1531px;left:0;width:1200px;height:607px;background:var(--ink)}
.services h2{top:96px;left:98px;font-family:'Poppins',sans-serif;font-weight:600;font-size:32px;color:var(--white)}
.service-item{position:absolute;left:98px;display:flex;align-items:center;gap:15px;font-family:'Poppins',sans-serif;font-size:19px;color:var(--white)}
.service-item .diamond{width:13px;height:13px;background:var(--white);transform:rotate(45deg)}
.service-item.active{color:var(--green);font-weight:600}
.service-item.active .diamond{background:var(--green)}
.service-photo{top:1451px;left:626px;width:475px;height:509px;background:linear-gradient(180deg,#d8e4ee 0%,#9eb1bd 35%,#7d5249 55%,#4a5560 80%,#b7b8b5 100%)}
.service-caption{top:1960px;left:626px;width:475px;height:78px;background:var(--green);display:flex;align-items:center;justify-content:center;font-family:'Poppins',sans-serif;font-weight:600;font-size:19px;color:var(--white)}

/* team */
.card-back{border:2px solid var(--green);border-radius:8px}
.card-back.dark{border-color:var(--ink)}
.team-card{background:var(--white);border-radius:8px;box-shadow:0 4px 18px rgba(0,0,0,.1)}
.team-photo{position:absolute;top:23px;left:26px;width:355px;height:297px;border-radius:6px}
.team-name{position:absolute;top:350px;left:0;width:406px;text-align:center;font-family:'Poppins',sans-serif;font-weight:600;font-size:25px;color:var(--ink)}
.team-role{position:absolute;top:390px;left:0;width:406px;text-align:center;font-family:'Poppins',sans-serif;font-size:17px;color:var(--ink)}
.team-role.accent{color:var(--green)}
.team-rule{position:absolute;top:425px;left:110px;width:186px;height:2px;background:var(--line)}
.team-contact{position:absolute;top:448px;display:flex;align-items:center;gap:14px;font-family:'Poppins',sans-serif;font-size:16px;color:var(--ink)}
.icon-circle{width:42px;height:42px;border-radius:50%;background:var(--green);display:flex;align-items:center;justify-content:center}
.icon-circle.dark{background:var(--ink)}

/* contact */
.contact{top:2940px;left:0;width:1200px;height:547px;background:var(--light)}
.field{position:absolute;background:var(--white);border-radius:6px;box-shadow:0 2px 8px rgba(0,0,0,.06);font-size:14px;color:#777;padding:18px 18px 0}
.submit{position:absolute;top:398px;left:530px;width:137px;height:51px;border-radius:30px;background:var(--ink);color:var(--white);display:flex;align-items:center;justify-content:center;font-family:'Poppins',sans-serif;font-weight:600;font-size:16px}

/* footer */
.site-footer{top:3487px;left:0;width:1200px;height:409px;background:#000}
.footer-brand .brand-name{color:var(--white);font-size:26px}
.footer-col h4{font-family:'Poppins',sans-serif;font-weight:600;font-size:21px;color:var(--white);margin-bottom:14px}
.footer-col li{list-style:none;display:flex;align-items:center;gap:12px;font-size:15px;color:var(--white);height:31px}
.contact-row{position:absolute;display:flex;align-items:center;gap:16px;font-size:15px;line-height:25px;color:var(--white)}
.footer-rule{top:338px;left:98px;width:1003px;height:1px;background:#666}
.copyright{top:364px;left:0;width:1200px;text-align:center;font-size:15px;color:var(--white)}
</style>
</head>
<body>

<header class="abs site-header">
  <div class="abs brand" style="top:24px;left:98px">
    <span class="brand-dot"></span><span class="brand-name">Tollbrook Advisory</span>
  </div>
  <nav class="nav">
    <a style="left:666px">About</a>
    <a style="left:767px">Services</a>
    <a style="left:888px">Team</a>
  </nav>
  <div class="btn" style="top:21px;left:968px;width:133px;height:47px">Contact Us</div>
</header>

<section class="abs hero">
  <div class="abs hero-photo" role="img" aria-label="Two smiling colleagues reviewing a tablet in a bright office"></div>
  <h1 class="abs">Building Success in Southern California</h1>
  <p class="abs">At Tollbrook, we blend innovative strategies with local market expertise to guide your commercial real estate ventures.</p>
  <div class="btn" style="top:371px;left:98px;width:133px;height:46px">Get Started</div>
</section>

<h2 class="section-title" style="top:760px"><span class="accent">About Tollbrook</span> Advisory</h2>
<div class="section-rule" style="top:813px"></div>

<div class="abs about-frame-back"></div>
<div class="abs about-frame-front"></div>
<div class="abs about-photo" role="img" aria-label="A consultant presenting to a team around a meeting table"></div>

<div class="abs about-block" style="top:860px;left:642px;width:460px">
  <div style="display:flex;align-items:center;gap:18px">
    <svg width="50" height="46" viewBox="0 0 50 46" fill="none" stroke="#8ec6a8" stroke-width="2"><circle cx="25" cy="14" r="7"/><circle cx="10" cy="12" r="5"/><circle cx="40" cy="12" r="5"/><path d="M12 40c0-8 6-14 13-14s13 6 13 14"/><path d="M2 32c0-6 4-10 8-10"/><path d="M48 32c0-6-4-10-8-10"/></svg>
    <h3>Who we are</h3>
  </div>
  <p class="about-text" style="margin-top:10px">Welcome to Tollbrook Advisory, your trusted partner in navigating the complexities of the real estate and small business markets. Founded by industry veterans Owen Hartley and Daniel Reyes, we specialize in providing comprehensive services tailored to the unique needs of our clients.</p>
</div>
<div class="abs about-divider"></div>
<div class="abs about-block" style="top:1113px;left:642px;width:460px">
  <div style="display:flex;align-items:center;gap:18px">
    <svg width="50" height="46" viewBox="0 0 50 46" fill="none" stroke="#1f2a33" stroke-width="2"><circle cx="22" cy="25" r="17"/><circle cx="22" cy="25" r="10"/><circle cx="22" cy="25" r="3"/><path d="M22 25L44 5M38 5h6v6"/></svg>
    <h3>Our Mission</h3>
  </div>
  <p class="about-text" style="margin-top:10px">Whether you're a franchisee, a new restaurant owner, or a commercial real estate investor, our expertise in due diligence, ensures you make informed, strategic decisions.</p>
</div>
<div class="btn" style="top:1288px;left:642px;width:133px;height:47px">Read More</div>

<section class="abs services">
  <h2 class="abs">Tollbrook Services</h2>
  <div class="service-item" style="top:147px"><span class="diamond"></span>Franchise Development &amp; Launch</div>
  <div class="service-item" style="top:211px"><span class="diamond"></span>Due Diligence Services</div>
  <div class="service-item active" style="top:275px"><span class="diamond"></span>Building &amp; Construction Management</div>
  <div class="service-item" style="top:340px"><span class="diamond"></span>Investment Property Evaluation</div>
  <div class="service-item" style="top:404px"><span class="diamond"></span>Market Analysis &amp; Feasibility Studies</div>
  <div class="btn" style="top:469px;left:99px;width:133px;height:46px">Read More</div>
</section>
<div class="abs service-photo" role="img" aria-label="New commercial retail building with storefronts and parking"></div>
<div class="abs service-caption">Building &amp; Construction Management</div>

<h2 class="section-title" style="top:2215px"><span class="accent">Our</span> Team</h2>
<div class="section-rule" style="top:2270px"></div>

<div class="abs card-back" style="top:2313px;left:172px;width:408px;height:512px"></div>
<div class="abs team-card" style="top:2330px;left:157px;width:406px;height:510px">
  <div class="team-photo" role="img" aria-label="Portrait of principal Daniel Reyes" style="background:linear-gradient(160deg,#a89a86,#5e4e40)"></div>
  <div class="team-name">Daniel Reyes</div>
  <div class="team-role accent">Principal</div>
  <div class="team-rule"></div>
  <div class="team-contact" style="left:80px">
    <span class="icon-circle"><svg width="16" height="16" viewBox="0 0 24 24" fill="#fff"><path d="M6.6 10.8a15 15 0 006.6 6.6l2.2-2.2c.3-.3.7-.4 1-.2 1.1.4 2.3.6 3.6.6.6 0 1 .4 1 1V20c0 .6-.4 1-1 1A17 17 0 013 4c0-.6.4-1 1-1h3.5c.6 0 1 .4 1 1 0 1.3.2 2.5.6 3.6.1.3 0 .7-.2 1z"/></svg></span>Phone
  </div>
  <div class="team-contact" style="left:226px">
    <span class="icon-circle"><svg width="16" height="14" viewBox="0 0 24 20" fill="#fff"><path d="M2 2h20v3l-10 6L2 5z"/><path d="M2 8l10 6 10-6v10H2z"/></svg></span>Email
  </div>
</div>

<div class="abs card-back dark" style="top:2313px;left:636px;width:408px;height:512px"></div>
<div class="abs team-card" style="top:2330px;left:620px;width:406px;height:510px">
  <div class="team-photo" role="img" aria-label="Portrait of principal Owen Hartley" style="background:linear-gradient(180deg,#b7c6d4,#d9dce3 60%,#8b9098)"></div>
  <div class="team-name">Owen Hartley</div>
  <div class="team-role">Principal</div>
  <div class="team-rule"></div>
  <div class="team-contact" style="left:80px">
    <span class="icon-circle dark"><svg width="16" height="16" viewBox="0 0 24 24" fill="#fff"><path d="M6.6 10.8a15 15 0 006.6 6.6l2.2-2.2c.3-.3.7-.4 1-.2 1.1.4 2.3.6 3.6.6.6 0 1 .4 1 1V20c0 .6-.4 1-1 1A17 17 0 013 4c0-.6.4-1 1-1h3.5c.6 0 1 .4 1 1 0 1.3.2 2.5.6 3.6.1.3 0 .7-.2 1z"/></svg></span>Phone
  </div>
  <div class="team-contact" style="left:226px">
    <span class="icon-circle dark"><svg width="16" height="14" viewBox="0 0 24 20" fill="#fff"><path d="M2 2h20v3l-10 6L2 5z"/><path d="M2 8l10 6 10-6v10H2z"/></svg></span>Email
  </div>
</div>

<section class="abs contact">
  <h2 class="section-title" style="top:70px"><span class="accent">Contact</span> Us</h2>
  <div class="section-rule" style="top:126px"></div>
  <div class="field" style="top:165px;left:181px;width:411px;height:48px">Name</div>
  <div class="field" style="top:165px;left:605px;width:412px;height:48px">Email</div>
  <div class="field" style="top:227px;left:181px;width:411px;height:48px">Phone Number</div>
  <div class="field" style="top:227px;left:605px;width:412px;height:48px">Subject</div>
  <div class="field" style="top:289px;left:181px;width:836px;height:86px">Message</div>
  <div class="submit">Submit</div>
</section>

<footer class="abs site-footer">
  <div class="abs brand footer-brand" style="top:122px;left:98px">
    <span class="brand-dot" style="width:48px;height:48px"></span><span class="brand-name">Tollbrook Advisory</span>
  </div>
  <div class="abs footer-col" style="top:68px;left:419px">
    <h4>Quick Links</h4>
    <ul>
      <li><svg width="14" height="12" viewBox="0 0 14 12" fill="#fff"><path d="M0 5h9V1l5 5-5 5V7H0z"/></svg>About</li>
      <li><svg width="14" height="12" viewBox="0 0 14 12" fill="#fff"><path d="M0 5h9V1l5 5-5 5V7H0z"/></svg>Services</li>
      <li><svg width="14" height="12" viewBox="0 0 14 12" fill="#fff"><path d="M0 5h9V1l5 5-5 5V7H0z"/></svg>Team</li>
      <li><svg width="14" height="12" viewBox="0 0 14 12" fill="#fff"><path d="M0 5h9V1l5 5-5 5V7H0z"/></svg>Contact Us</li>
    </ul>
  </div>
  <div class="abs footer-col" style="top:68px;left:617px">
    <h4>Other Links</h4>
    <ul>
      <li><svg width="14" height="12" viewBox="0 0 14 12" fill="#fff"><path d="M0 5h9V1l5 5-5 5V7H0z"/></svg>FAQ</li>
      <li><svg width="14" height="12" viewBox="0 0 14 12" fill="#fff"><path d="M0 5h9V1l5 5-5 5V7H0z"/></svg>Terms of Use</li>
      <li><svg width="14" height="12" viewBox="0 0 14 12" fill="#fff"><path d="M0 5h9V1l5 5-5 5V7H0z"/></svg>Privacy Policy</li>
      <li><svg width="14" height="12" viewBox="0 0 14 12" fill="#fff"><path d="M0 5h9V1l5 5-5 5V7H0z"/></svg>Support Links</li>
      <li><svg width="14" height="12" viewBox="0 0 14 12" fill="#fff"><path d="M0 5h9V1l5 5-5 5V7H0z"/></svg>Conditions</li>
    </ul>
  </div>
  <div class="abs footer-col" style="top:68px;left:829px"><h4>Contact Us</h4></div>
  <div class="contact-row" style="top:127px;left:829px">
    <span class="icon-circle" style="width:38px;height:38px"><svg width="14" height="18" viewBox="0 0 14 18" fill="#fff"><path d="M7 0a7 7 0 017 7c0 5-7 11-7 11S0 12 0 7a7 7 0 017-7zm0 4a3 3 0 100 6 3 3 0 000-6z"/></svg></span>
    <span>412 Harbor View Ave Suite 200<br>Lakemont, CA 90000</span>
  </div>
  <div class="contact-row" style="top:198px;left:829px">
    <span class="icon-circle" style="width:38px;height:38px"><svg width="15" height="13" viewBox="0 0 24 20" fill="#fff"><path d="M2 2h20v3l-10 6L2 5z"/><path d="M2 8l10 6 10-6v10H2z"/></svg></span>
    <span>info@tollbrookadvisory.example</span>
  </div>
  <div class="contact-row" style="top:255px;left:829px">
    <span class="icon-circle" style="width:38px;height:38px"><svg width="15" height="15" viewBox="0 0 24 24" fill="#fff"><path d="M6.6 10.8a15 15 0 006.6 6.6l2.2-2.2c.3-.3.7-.4 1-.2 1.1.4 2.3.6 3.6.6.6 0 1 .4 1 1V20c0 .6-.4 1-1 1A17 17 0 013 4c0-.6.4-1 1-1h3.5c.6 0 1 .4 1 1 0 1.3.2 2.5.6 3.6.1.3 0 .7-.2 1z"/></svg></span>
    <span>+1 555 010 2040</span>
  </div>
  <div class="abs footer-rule"></div>
  <div class="abs copyright">Copyrights@2024.Tollbrook Advisory.All Rights Reserved</div>
</footer>

</body>
</html>
```